Letterhead for a German Distribution/Manufacturing Company

We need a professional Letterhead in a unique Design.
not to playful.
The Letterhead has to show show that we are a international company with headquater in Germany.
all details like adress, Vat Tax Number, Bank Accout, Eori, email, Company number has to be on the Letterhead.
for example use: VAT TAX DE5470318 Bank Account: Kestrel Bank IBAN DE412058731ß204683 Swift: MORV0417352 EORI 3150428697 Company Number: HRB 51806 Adress: VOLMINTA UG Ahornweg 7 Postal Code 06384 City Altwendel Country: Germany Email: info@volminta-example.com
the design can be colored but doesnt have to be
Industry/Entity Type
Manufacturing and international distribution
Requirements
Must have
- show that we are a international company with headquater in Germany. our company infos and logo

```html
<!DOCTYPE html>
<html lang="en">
<head>
<meta charset="utf-8">
<title>VOLMINTA Letterhead</title>
<link href="https://fonts.googleapis.com/css2?family=Roboto:wght@300;400;500&display=swap" rel="stylesheet">
<style>
  :root {
    --backdrop: #e6e6e7;
    --paper: #ffffff;
    --ink: #1d1d1d;
    --ink-soft: #2e2e2e;
    --band: #1f1f1f;
    --band-text: #f2f2f2;
    --rule: #333333;
    --signature-tone: #d9d9d9;
  }
  * { margin: 0; padding: 0; box-sizing: border-box; }
  html, body {
    width: 1200px;
    height: 874px;
    overflow: hidden;
    background: var(--backdrop);
    font-family: "Roboto", Arial, sans-serif;
    color: var(--ink);
  }
  .letterhead {
    position: absolute;
    left: 310px;
    top: 22px;
    width: 580px;
    height: 830px;
    background: var(--paper);
    box-shadow: 0 2px 10px rgba(0,0,0,0.08);
  }
  .brand {
    position: absolute;
    left: 52px;
    top: 54px;
    display: flex;
    align-items: center;
    gap: 10px;
  }
  .brand-dot {
    width: 30px;
    height: 30px;
    border-radius: 50%;
    background: var(--ink);
  }
  .brand-name {
    font-size: 34px;
    font-weight: 400;
    letter-spacing: 1px;
    color: var(--ink);
  }
  .company-address {
    position: absolute;
    right: 52px;
    top: 46px;
    padding-left: 14px;
    border-left: 1px solid var(--rule);
    font-size: 9.5px;
    line-height: 13px;
    font-weight: 400;
    font-style: normal;
    color: var(--ink-soft);
  }
  .company-address .mail-icon {
    display: inline-block;
    vertical-align: -1px;
    margin-right: 4px;
  }
  .recipient {
    position: absolute;
    left: 52px;
    top: 178px;
    font-size: 11px;
    line-height: 15px;
  }
  .letter-body {
    position: absolute;
    left: 52px;
    top: 258px;
    width: 476px;
    font-size: 10.5px;
    line-height: 15.5px;
    font-weight: 400;
    color: var(--ink-soft);
  }
  .letter-body p { margin-bottom: 14px; }
  .closing {
    position: absolute;
    left: 52px;
    top: 566px;
    font-size: 11px;
  }
  .signature {
    position: absolute;
    left: 52px;
    top: 590px;
    width: 140px;
    height: 50px;
    background: linear-gradient(90deg, var(--signature-tone), #f3f3f3);
    border-radius: 4px;
  }
  .footer-band {
    position: absolute;
    left: 0;
    right: 0;
    bottom: 32px;
    height: 66px;
    background: var(--band);
    color: var(--band-text);
    display: flex;
    align-items: center;
    padding: 0 40px 0 52px;
    font-size: 10px;
    line-height: 16px;
    font-weight: 400;
    white-space: nowrap;
  }
  .footer-registry { width: 150px; }
  .footer-divider {
    width: 1px;
    height: 34px;
    background: var(--band-text);
    margin: 0 16px;
  }
</style>
</head>
<body>
  <main class="letterhead">
    <header>
      <div class="brand">
        <span class="brand-dot"></span>
        <span class="brand-name">VOLMINTA</span>
      </div>
      <address class="company-address">
        VOLMINTA UG Ahornweg 7<br>
        Postal Code 06384 City Altwendel<br>
        Country: Germany<br>
        <svg class="mail-icon" width="9" height="7" viewBox="0 0 9 7" aria-hidden="true"><rect x="0.5" y="0.5" width="8" height="6" fill="none" stroke="#2e2e2e"/><path d="M0.5 0.5 L4.5 4 L8.5 0.5" fill="none" stroke="#2e2e2e"/></svg>info@volminta-example.com
      </address>
    </header>

    <section class="recipient">
      Mr/s<br>
      First Name and Last Name<br>
      Company Name<br>
      Address
    </section>

    <section class="letter-body">
      <p>Lorem Ipsum is simply dummy text of the printing and typesetting industry. Lorem Ipsum has been the industry's standard dummy text ever since the 1500s, when an unknown printer took a galley of type and scrambled it to make a type specimen book. It has survived not only five centuries, but also the leap into electronic typesetting, remaining essentially unchanged. It was popularised in the 1960s with the release of Dravello sheets containing Lorem Ipsum passages.</p>
      <p>he standard chunk of Lorem Ipsum used since the 1500s is reproduced below for those interested. Sections 1.10.32 and 1.10.33 from "de Finibus Bonorum et Malorum" by Aurelian Dax are also reproduced in their exact original form, accompanied by English versions from the 1914 translation by H. Bramley. Lorem ipsum dolor sit amet, consectetur adipiscing elit, sed do eiusmod tempor incididunt ut labore et dolore magna aliqua.</p>
      <p>It is a long established fact that a reader will be distracted by the readable content of a page when looking at its layout. The point of using Lorem Ipsum is that it has a more-or-less normal distribution of letters, as opposed to using 'Content here, content here', making it look like readable English. Many desktop publishing packages and web page editors now .</p>
    </section>

    <div class="closing">Your Sincerely,</div>
    <div class="signature" role="img" aria-label="Handwritten signature"></div>

    <footer class="footer-band">
      <div class="footer-registry">
        VAT TAX DE5470318<br>
        Company Number: HRB 51806
      </div>
      <div class="footer-divider"></div>
      <div class="footer-banking">
        Bank Account: Kestrel Bank IBAN DE412058731ß204683<br>
        Swift: MORV0417352 EORI 3150428697
      </div>
    </footer>
  </main>
</body>
</html>
```